Magazine Template for National Charity

We need a magazine design for an Australian youth charity called Rhythm Crews Lifting FUtures (RCLF). We engage young people through street culture music, dance and mentoring programs, and help them to turn their lives around. Our charity's vision is to see every young person have someone who believes in them and the opportunity to live their potential.

The design should have places for images of our young people during programs(we've only provided a few for you), room for quotes from young people and supporters etc, and each double spread could be a snapshot of a different program.

We will need a design template that will allow us to add all the contents for the magazine, including a contents page, report from our Chairman (1 page), letter from CEO (1 page), and following achievements of our programs including 1. RCLF Camps (2 x double spread, total 4 pages), 2. Groove Labs (2 x double spread, total 4 pages) and 3. Mentoring (2 x double spread, total 4 pages). An audited financial report of 4 pages will be copied in after our program reports, and on the back of the magazine, we'll need space for all our supporter logos. I'd also like to include a short story or case-study about young people's transformation on each program page.

We need something that's got a bit of a street edge, to keep our youthful brand, but helps us to highlight our excellence as an innovative and cutting edge charity. The final design should be emotional, eye-catching, reflective of our creative spark, and inspiring. We currently have a brand that uses a fair bit of black & white with highlights of colour, however I dont want this to limit your creativity. We use a font called Octin Spraypaint Free for our logos and program names.

We would like to present our annual report as a magazine so that it is something that people will want to pick up and look at.

Target Market(s)

This is for general public and supporters, however we'd like to use our brand instead of a professional style for this report

Industry/Entity Type

Financial

Requirements
Must have
• See notes in task description - thank you!

We will give you a few images to use as a guide however we'd love to be able to play around with the images once we have a template (we'll add different ones and change pictures around to suit the program pages). We're providing these images so that you can get a feel for our culture and be inspired to put together the template, dont worry if you use the same photos more than once on the different pages to show as an example.
Nice to have
• We already have our charity logo, however we'd love to call this RCLF Mag, RCLF Magazine or Newest RCLF Rhythmania. We'd like it to replicate a real magazine, with colour and lots of interesting sections for information & stories, rather than a boring traditional annual report template.
Should not have
• We want this magazine to stand out, and we dont want a half-hearted charity design or a polished corporate style magazine.

We want to remain bold and contemporary, and on the commercial side with a street edge - have lots of fun & thank you so much - we're very excited!

```html
<!DOCTYPE html>
<html lang="en">
<head>
<meta charset="utf-8">
<title>RCLF Mag – Groove Labs Spread</title>
<link rel="stylesheet" href="https://fonts.googleapis.com/css2?family=Big+Shoulders+Stencil+Display:wght@600;700&family=Signika:wght@400;700&display=swap">
<style>
  :root {
    --spread-green: #63f303;
    --ink-white: #ffffff;
    --heading-orange: #f2801f;
    --logo-ink: #1c1c1c;
    --photo-mono-light: #d9d9d9;
    --photo-mono-dark: #3a3a3a;
    --photo-warm-light: #e9d2b8;
    --photo-warm-dark: #5a4436;
    --photo-colour-light: #b9a06a;
    --photo-colour-dark: #3b3226;
  }
  * { box-sizing: border-box; margin: 0; padding: 0; }
  html, body { width: 1200px; height: 855px; overflow: hidden; }
  body {
    background: var(--spread-green);
    font-family: "Signika", "Trebuchet MS", sans-serif;
    color: var(--ink-white);
    position: relative;
  }
  .spread { position: absolute; inset: 0; width: 1200px; height: 855px; }
  .page { position: absolute; top: 0; height: 855px; width: 600px; }
  .page--left { left: 0; }
  .page--right { left: 600px; }

  .display {
    font-family: "Big Shoulders Stencil Display", "Impact", sans-serif;
    font-weight: 600;
    text-transform: uppercase;
    color: var(--ink-white);
    letter-spacing: 1px;
  }

  /* program badge */
  .program-badge {
    position: absolute; left: 41px; top: 47px;
    width: 116px; height: 116px; border-radius: 50%;
    background: var(--ink-white);
    display: flex; align-items: center; justify-content: center;
  }
  .program-badge__label {
    transform: rotate(-15deg);
    font-size: 17px; line-height: 17px; text-align: center;
    color: var(--spread-green);
  }

  .feature-quote {
    position: absolute; left: 47px; top: 170px;
    font-size: 66px; line-height: 70px;
  }

  .photo { position: absolute; border-radius: 50%; }
  .photo--lead {
    left: 48px; top: 350px; width: 304px; height: 304px;
    background: radial-gradient(circle at 40% 45%, var(--photo-mono-light), var(--photo-mono-dark));
  }
  .photo--small {
    left: 33px; top: 50px; width: 134px; height: 134px;
    background: radial-gradient(circle at 55% 40%, var(--photo-warm-light), var(--photo-warm-dark));
  }
  .photo--side {
    left: 323px; top: 488px; width: 223px; height: 223px;
    background: radial-gradient(circle at 50% 45%, var(--photo-colour-light), var(--photo-colour-dark));
  }

  .story { position: absolute; font-size: 10px; line-height: 13px; font-weight: 400; }
  .story__heading {
    font-weight: 700; font-size: 10.5px; line-height: 13px; color: var(--heading-orange);
    letter-spacing: 0.3px;
  }
  .story p { margin-bottom: 13px; }
  .story--left { left: 368px; top: 425px; width: 205px; }
  .story--top-right { left: 215px; top: 103px; width: 295px; }
  .story--bottom-right { left: 58px; top: 535px; width: 250px; text-align: right; }

  .pull-quote {
    position: absolute; right: 53px; top: 314px;
    font-size: 40px; line-height: 40px; text-align: right;
  }

  .masthead {
    position: absolute; right: 53px; top: 15px;
    width: 135px; height: 33px;
    background: var(--ink-white); border-radius: 0 0 8px 8px;
    display: flex; align-items: center; gap: 5px; padding: 0 6px;
  }
  .masthead__dot { width: 9px; height: 9px; border-radius: 50%; background: var(--logo-ink); flex: none; }
  .masthead__name {
    font-weight: 700; font-size: 9px; line-height: 10px;
    color: var(--logo-ink); text-transform: uppercase;
  }

  .folio {
    position: absolute; bottom: 20px;
    display: flex; align-items: center; gap: 6px;
    font-size: 10px;
  }
  .folio--left { left: 47px; }
  .folio--right { right: 53px; }
  .folio__number {
    width: 20px; height: 19px; background: var(--ink-white);
    color: var(--spread-green); font-weight: 700; font-size: 11px;
    display: flex; align-items: center; justify-content: center;
    border-radius: 0 4px 0 0;
  }
</style>
</head>
<body>
<main class="spread">
  <section class="page page--left">
    <div class="program-badge">
      <span class="program-badge__label display">The<br>Groove<br>Labs</span>
    </div>

    <h1 class="feature-quote display">“Ak dedef eaaf<br>pajed tofdu”</h1>

    <div class="photo photo--lead" role="img" aria-label="Black and white photo of a smiling young participant in a striped top at a program session"></div>

    <article class="story story--left">
      <h2 class="story__heading">HEADING</h2>
      <p>Young people from across the city gathered each week to write, record and perform their own tracks, backed by mentors who truly believe in them and their ideas.</p>
      <p>Crews shared beats, bars and stories, building trust and confidence with every single session they attended together.</p>
      <p>By the end of the term the group had staged a live showcase for family and friends, with every voice heard. Many have since signed up to lead new crews of their own, passing on the skills they learned and the belief they found in the room each week. Local venues have offered stages for the next round of shows.</p>
      <p>Next year the program grows to three new sites, reaching even more young people who need a place to belong, a beat to follow and a mentor to lean on.</p>
    </article>

    <footer class="folio folio--left">
      <span class="folio__number">14</span>
      <span class="folio__tagline">live your full potential</span>
    </footer>
  </section>

  <section class="page page--right">
    <div class="masthead">
      <span class="masthead__dot"></span>
      <span class="masthead__name">Rhythm Crews<br>Lifting Futures</span>
    </div>

    <div class="photo photo--small" role="img" aria-label="Photo of a young woman singing into a microphone on stage"></div>

    <article class="story story--top-right">
      <h2 class="story__heading">HEADING</h2>
      <p>Our mentors met young people where they are, using music to open doors and start real conversations about the future ahead.</p>
      <p>Every track told a story of change, courage and the power of having someone in your corner, week after week.</p>
      <p>Participants left with new skills, new friends and a clear plan for the next step in their journey.</p>
    </article>

    <blockquote class="pull-quote display">“Ak dedef eaaf pajed tofdu<br>dfjf jdfdshjf jadfkhjhfj<br>ajfhjdfkjhdlkh djfhdlhf”</blockquote>

    <article class="story story--bottom-right">
      <h2 class="story__heading">HEADING</h2>
      <p>Dance, rap and production workshops gave each crew the space to try something new and shine in front of their peers.</p>
      <p>Weekly sessions built routines, respect and a real sense of belonging for everyone involved.</p>
      <p>Families joined the final night to cheer on a group that had grown stronger together, proud of every step they took.</p>
    </article>

    <div class="photo photo--side" role="img" aria-label="Photo of a young dancer performing in front of a colourful mural"></div>

    <footer class="folio folio--right">
      <span class="folio__site">www.rclf.org.au</span>
      <span class="folio__number">15</span>
    </footer>
  </section>
</main>
</body>
</html>
```